Hello my Name is Elias Moreno. I buy and sell vintage comic books, you can refer to my instragram page qpkz.comics to get ideas and inspiration. For the front of the card I would like my company logo QPKZ Comics with a yellow and black background with the bat signal or bat emblem like on my IG page and with my info Elias Moreno as the Owner and address/ phone number, PO Box 617283, Miami, FL 33827, 305-482-6170 and that I buy and sell comics & collectables . Also feel free to be open to other ideas if you want. Im not stuck on one design. For the back of the card I would like for it to say follow me on Instagram QPKZ.Comics with the ig emblem. Also would like the card to be vertical if possible. Thanks

```html
<!DOCTYPE html>
<html lang="en">
<head>
<meta charset="utf-8">
<title>QPKZ Comics – Business Card</title>
<link href="https://fonts.googleapis.com/css2?family=Source+Sans+3:wght@400;600;700;800&display=swap" rel="stylesheet">
<style>
  :root {
    --stage-top: #2b2b2b;
    --stage-bottom: #050505;
    --card-yellow-start: #f1bd1c;
    --card-yellow-end: #fac918;
    --card-white-start: #ececec;
    --card-white-end: #fbfbfb;
    --ink: #111111;
    --ink-soft: #2a2a2a;
  }
  * { margin: 0; padding: 0; box-sizing: border-box; }
  html, body {
    width: 1200px;
    height: 900px;
    overflow: hidden;
  }
  body {
    position: relative;
    background: linear-gradient(180deg, var(--stage-top) 0%, var(--stage-bottom) 100%);
    font-family: "Source Sans 3", "Myriad Pro", Arial, sans-serif;
    color: var(--ink);
  }
  .card {
    position: absolute;
    top: 300px;
    width: 442px;
    height: 273px;
    border-radius: 10px;
    box-shadow: 0 4px 14px rgba(0, 0, 0, 0.45);
  }
  .card--front {
    left: 152px;
    background: linear-gradient(120deg, var(--card-yellow-start) 0%, var(--card-yellow-end) 100%);
  }
  .card--back {
    left: 622px;
    background: linear-gradient(120deg, var(--card-white-start) 0%, var(--card-white-end) 100%);
  }
  .brand-mark {
    position: absolute;
    display: flex;
    flex-direction: column;
    align-items: center;
    justify-content: center;
    gap: 10px;
    width: 180px;
    height: 140px;
    font-weight: 800;
    font-size: 34px;
    line-height: 1;
    letter-spacing: 1px;
    color: var(--ink);
    text-align: center;
  }
  .brand-mark__dot {
    width: 22px;
    height: 22px;
    border-radius: 50%;
    background: var(--ink);
  }
  .card--front .brand-mark { left: 49px; top: 57px; }
  .card--back .brand-mark { left: 131px; top: 57px; }
  .tagline {
    position: absolute;
    left: 0;
    width: 278px;
    top: 214px;
    text-align: center;
    font-size: 13px;
    font-weight: 400;
    color: var(--ink);
  }
  .contact {
    position: absolute;
    left: 274px;
    top: 52px;
    font-size: 17px;
    line-height: 1.35;
    color: var(--ink-soft);
  }
  .contact__name {
    font-weight: 700;
    font-size: 18px;
    color: var(--ink);
    text-transform: uppercase;
  }
  .contact__role { margin-bottom: 20px; }
  .contact__phone {
    display: flex;
    align-items: center;
    gap: 4px;
    font-size: 17px;
    margin-bottom: 52px;
  }
  .contact__phone svg { width: 13px; height: 13px; }
  .contact__address { line-height: 1.15; }
  .follow {
    position: absolute;
    left: 0;
    width: 100%;
    top: 232px;
    display: flex;
    justify-content: center;
    align-items: center;
    gap: 6px;
    font-size: 13px;
    color: var(--ink);
  }
  .follow__square {
    width: 15px;
    height: 15px;
    border-radius: 3px;
    background: var(--ink);
  }
</style>
</head>
<body>
  <section class="card card--front">
    <div class="brand-mark">
      <span class="brand-mark__dot"></span>
      <span>QPKZ Comics</span>
    </div>
    <p class="tagline">We buy and sell comics &amp; collectables</p>
    <div class="contact">
      <p class="contact__name">Elias Moreno</p>
      <p class="contact__role">Owner</p>
      <p class="contact__phone">
        <svg viewBox="0 0 24 24" aria-hidden="true"><path fill="#111" d="M6.6 10.8a15 15 0 0 0 6.6 6.6l2.2-2.2a1 1 0 0 1 1-.25 11.4 11.4 0 0 0 3.6.57 1 1 0 0 1 1 1V20a1 1 0 0 1-1 1A17 17 0 0 1 3 4a1 1 0 0 1 1-1h3.5a1 1 0 0 1 1 1c0 1.25.2 2.46.57 3.6a1 1 0 0 1-.25 1z"/></svg>
        305-482-6170
      </p>
      <p class="contact__address">PO Box 617283,<br>Miami, FL 33827</p>
    </div>
  </section>

  <section class="card card--back">
    <div class="brand-mark">
      <span class="brand-mark__dot"></span>
      <span>QPKZ Comics</span>
    </div>
    <p class="follow">Follow me on <span class="follow__square"></span> QPKZ.Comics</p>
  </section>
</body>
</html>
```